Brightwave Reach - Business Card

We need a business card for a Social Media Marketing company that specializes in online marketing for small businesses in Canada using common Social Media platforms such as Pixlora, Chatterly, Blinkpost & Quibber.

I have uploaded a copy of our logo which I would like utilized in the business card. We would like the business card to be modern yet classy design.

Our website is www.brightwavereach.ca

Industry/Entity Type

Marketing

Contact Information for Business Card

Email: info@brightwavereach.ca
Website: www.brightwavereach.ca
Telephone: 604-555-0193

Colors

Designer to choose colors to be used in the design.

Requirements
Must have
• Social Media icons on reverse
• Please add some designs with color.

```html
<!DOCTYPE html>
<html lang="en">
<head>
<meta charset="utf-8">
<title>Brightwave Reach – Business Card</title>
<link rel="stylesheet" href="https://fonts.googleapis.com/css2?family=Josefin+Sans:wght@300;400;600&display=swap">
<style>
  :root {
    --backdrop: #2a2a2a;
    --card: #f4f4f2;
    --ink: #3a3a3a;
    --ink-soft: #555555;
    --accent: #2fb3d1;
    --leaf: #3b3b3b;
  }
  * { margin: 0; padding: 0; box-sizing: border-box; }
  html, body {
    width: 1200px;
    height: 900px;
    overflow: hidden;
    background: var(--backdrop);
  }
  .canvas {
    position: relative;
    width: 1200px;
    height: 900px;
    font-family: "Josefin Sans", sans-serif;
  }
  .card {
    position: absolute;
    width: 560px;
    height: 320px;
    background: var(--card);
    box-shadow: 0 10px 24px rgba(0, 0, 0, 0.45);
  }
  .card--front { left: 100px; top: 110px; }
  .card--back  { left: 540px; top: 480px; }

  /* Front */
  .brand {
    position: absolute;
    left: 50%;
    top: 50%;
    transform: translate(-50%, -50%);
    display: flex;
    align-items: center;
    gap: 14px;
  }
  .brand__mark {
    width: 18px;
    height: 18px;
    background: var(--ink);
  }
  .brand__name {
    font-weight: 600;
    font-size: 30px;
    letter-spacing: 1px;
    text-transform: uppercase;
    color: var(--ink);
  }

  /* Back */
  .leaf {
    position: absolute;
    right: 58px;
    top: 36px;
    width: 68px;
    height: 72px;
  }
  .accent-bar {
    position: absolute;
    right: 0;
    top: 210px;
    width: 150px;
    height: 9px;
    background: var(--accent);
  }
  .contact {
    position: absolute;
    left: 44px;
    bottom: 40px;
    color: var(--ink);
  }
  .contact__social {
    display: flex;
    gap: 12px;
    font-size: 11px;
    font-weight: 600;
    letter-spacing: 1px;
    color: var(--ink-soft);
    margin-bottom: 12px;
  }
  .contact__line {
    font-weight: 300;
    font-size: 17px;
    letter-spacing: 2.4px;
    line-height: 27px;
  }
</style>
</head>
<body>
<main class="canvas">
  <section class="card card--front" aria-label="Card front">
    <div class="brand">
      <span class="brand__mark"></span>
      <span class="brand__name">Brightwave Reach</span>
    </div>
  </section>

  <section class="card card--back" aria-label="Card back">
    <svg class="leaf" role="img" aria-label="Textured maple leaf emblem" viewBox="0 0 68 72">
      <rect width="68" height="72" rx="6" fill="var(--leaf)"/>
    </svg>
    <div class="accent-bar"></div>
    <div class="contact">
      <div class="contact__social">
        <span>Chatterly</span>
        <span>Quibber</span>
        <span>Pixlora</span>
      </div>
      <p class="contact__line">info@brightwavereach.ca</p>
      <p class="contact__line">www.brightwavereach.ca</p>
      <p class="contact__line">604-555-0193</p>
    </div>
  </section>
</main>
</body>
</html>
```